Oriel Photography Business Card

I need a business card designed for a photography business based in Perth, Western Australia called Oriel Photography.

We specialise in wedding, event photography and portrait photography.

The business card must borrow the style of the attached logo.

The hex codes for the colours in the logo are:
#ED1D85 - Pink
#89C23E - Green
#37282F - Black

The name on the card will be:
Name: Tobrian
Phone: 0417395268
Website: www.orielphotography.example.com.au
social: orielphotography

I am open and happy to accept creative concepts.

I’d like some space at the back for writing notes and appointment details.

```html
<!DOCTYPE html>
<html lang="en">
<head>
<meta charset="utf-8">
<title>Oriel Photography – Business Card</title>
<link rel="stylesheet" href="https://fonts.googleapis.com/css2?family=Arimo:wght@400;700&family=Questrial&display=swap">
<style>
  :root {
    --pink: #ED1D85;
    --green: #89C23E;
    --lime: #9BE71E;
    --ink: #37282F;
    --grey: #9A9A9A;
    --paper: #FFFFFF;
    --backdrop: #ECE9E4;
  }
  * { box-sizing: border-box; margin: 0; padding: 0; }
  html, body { width: 1200px; height: 1000px; overflow: hidden; }
  body { background: var(--backdrop); position: relative; font-family: "Arimo", sans-serif; }

  .card {
    position: absolute;
    width: 560px; height: 340px;
    background: var(--paper);
    box-shadow: 0 6px 18px rgba(0,0,0,0.12);
    overflow: hidden;
  }
  .card--front { left: 60px; top: 120px; }
  .card--back  { left: 580px; top: 500px; }

  .brand-mark {
    position: absolute;
    width: 74px; height: 74px;
    border-radius: 50%;
    background: var(--pink);
  }
  .card--front .brand-mark { left: 243px; top: 62px; }
  .card--back  .brand-mark { left: 243px; top: 34px; }

  .wordmark {
    position: absolute;
    font-family: "Questrial", sans-serif;
    color: var(--ink);
    font-size: 17px;
    letter-spacing: 0.62em;
    text-transform: uppercase;
    white-space: nowrap;
  }
  .card--front .wordmark { left: 0; right: 0; top: 158px; text-align: center; }
  .card--back  .wordmark { left: 92px; top: 122px; }

  .tagline {
    position: absolute;
    left: 0; right: 0; top: 188px;
    text-align: center;
    font-size: 16px;
    color: var(--grey);
    letter-spacing: 0.06em;
  }

  .front-rule {
    position: absolute; left: 0; right: 0; top: 262px;
    height: 3px; background: var(--pink);
  }
  .front-band {
    position: absolute; left: 0; right: 0; top: 270px; bottom: 0;
    background: var(--lime);
  }

  .holder-name {
    position: absolute; right: 30px; top: 66px;
    font-weight: 700; font-size: 20px; color: var(--pink);
  }

  .back-rule-dark {
    position: absolute; left: 0; right: 0; top: 152px;
    height: 3px; background: var(--ink);
  }
  .back-rule-green {
    position: absolute; left: 0; right: 0; top: 157px;
    height: 3px; background: var(--lime);
  }

  .contact-list {
    position: absolute; left: 40px; top: 200px;
    list-style: none;
  }
  .contact-item {
    display: flex; align-items: center; gap: 8px;
    height: 30px;
    font-size: 20px; color: var(--lime);
    letter-spacing: 0.02em;
  }
  .contact-badge {
    width: 24px; height: 24px;
    background: var(--pink);
    color: var(--paper);
    font-weight: 700; font-size: 17px;
    display: flex; align-items: center; justify-content: center;
    border-radius: 2px;
  }
</style>
</head>
<body>
  <section class="card card--front" aria-label="Card front">
    <div class="brand-mark"></div>
    <p class="wordmark">Oriel Photography</p>
    <p class="tagline">Wedding-Event Photography-Portrait Photography</p>
    <div class="front-rule"></div>
    <div class="front-band"></div>
  </section>

  <section class="card card--back" aria-label="Card back">
    <div class="brand-mark"></div>
    <p class="holder-name">Tobrian</p>
    <p class="wordmark">Oriel Photography</p>
    <div class="back-rule-dark"></div>
    <div class="back-rule-green"></div>
    <ul class="contact-list">
      <li class="contact-item"><span class="contact-badge">P</span>0417395268</li>
      <li class="contact-item"><span class="contact-badge">W</span>www.orielphotography.example.com.au</li>
      <li class="contact-item"><span class="contact-badge"></span>social/orielphotography</li>
    </ul>
  </section>
</body>
</html>
```